Business Card Design

educational services
broker of essential services
So I love my The Velvet Kettle cards. I love the background.
I like the background on the copper valley card
I like a little part of each Meridel card
I want my card to stand out and be professional
I would also like somewhat of a brand
I do not want it to be specific to anything but the world and galaxy
I would like to be able to be used for everything, all encompassing
In spanish Cielo abierto, not sureother languages but i will do programs for other countries like China, Japan and Korea
Reason: It has been the first week of school and I have not been able to get the feedback I need.
Please change colors to Blue and GOld
Please add ~ over the n in Lorna
Please submit some vertical designs
Please include the world
Please make eagle a watermark
Make sure the Open Horizon doesnt have "preparatory school" under it
I am open to new designs and I will pay more after I chose a designer who seems to get all this stuff in my head!
Reason: Last minute designs were wonderful
Reason: I was out of town and not able to review the wonderful designs posted. I am narrowing the designs down now! I appreciate all the work done thus far.
Hello,
Thank you for all the designs. This is difficult. I have not been able to access them as I was able to last week so please be patient. If you also do web design please send me a message.
Again, thank you. I am down to just a few designs.
Sincerely,
Lorna Vickers Dunmore
I have been extremely busy, I should pick a design by the ned of this week. Thank you for your patience
Industry/Entity Type
Business
Contact Information for Business Card
Dr. Lorna Vickers Dunmore
www.ohacad.example
(555) 284-9306 US
lornajeanvickers@mailbox.example

```html
<!DOCTYPE html>
<html lang="en">
<head>
<meta charset="utf-8">
<title>Open Horizon – Business Card</title>
<link rel="stylesheet" href="https://fonts.googleapis.com/css2?family=Lobster&family=Montserrat:wght@500;600&family=Roboto:wght@400;700&display=swap">
<style>
  :root {
    --page-bg: #ededee;
    --navy-deep: #0a2a5e;
    --navy: #0b3f86;
    --royal: #1a63b8;
    --gold: #f2b80f;
    --gold-text: #f6c21a;
    --ice: #dbe9f6;
    --ice-light: #e8f1fa;
    --globe-pale: #e3eef9;
    --ink-navy: #12306a;
    --link-blue: #2a7fd4;
    --white: #ffffff;
  }
  * { box-sizing: border-box; margin: 0; padding: 0; }
  html, body { width: 1200px; height: 977px; overflow: hidden; }
  body {
    background: var(--page-bg);
    position: relative;
    font-family: "Roboto", Arial, sans-serif;
  }
  .card {
    position: absolute;
    width: 530px;
    height: 303px;
    top: 337px;
    overflow: hidden;
    box-shadow: 0 6px 18px rgba(0,0,0,0.12);
  }

  /* Front side */
  .card-front {
    left: 50px;
    background: radial-gradient(ellipse at 50% 45%, var(--royal) 0%, var(--navy) 55%, var(--navy-deep) 100%);
  }
  .world-globe {
    position: absolute;
    left: 175px;
    top: 61px;
    width: 180px;
    height: 180px;
    border-radius: 50%;
    background: radial-gradient(circle at 45% 40%, var(--globe-pale) 0%, #cfe0f3 100%);
  }
  .world-globe .continents {
    position: absolute;
    inset: 0;
    border-radius: 50%;
    background: radial-gradient(ellipse at 45% 45%, rgba(26,99,184,0.55) 0%, rgba(26,99,184,0.25) 45%, rgba(26,99,184,0) 70%);
  }
  .tagline {
    position: absolute;
    left: 150px;
    top: 102px;
    width: 230px;
    text-align: center;
    font-family: "Lobster", cursive;
    font-size: 21px;
    line-height: 1.15;
    color: var(--gold-text);
    transform: rotate(14deg);
    text-shadow: 0 0 2px var(--navy-deep), 0 0 2px var(--navy-deep);
  }

  /* Back side */
  .card-back {
    left: 620px;
    background: linear-gradient(160deg, var(--ice-light) 0%, var(--ice) 100%);
  }
  .brand-band {
    position: absolute;
    left: 0;
    top: 34px;
    width: 100%;
    height: 84px;
    background: linear-gradient(90deg, var(--navy-deep) 0%, var(--navy) 45%, var(--royal) 100%);
    border-top: 3px solid var(--gold);
    border-bottom: 3px solid var(--gold);
  }
  .brand-name {
    position: absolute;
    right: 22px;
    top: 50%;
    transform: translateY(-50%);
    display: flex;
    align-items: center;
    gap: 10px;
    font-family: "Montserrat", Arial, sans-serif;
    font-weight: 600;
    font-size: 30px;
    letter-spacing: 1px;
    color: var(--white);
  }
  .brand-dot {
    width: 26px;
    height: 26px;
    border-radius: 50%;
    background: var(--white);
  }
  .contact-block {
    position: absolute;
    left: 196px;
    top: 136px;
  }
  .contact-name {
    font-weight: 700;
    font-size: 15px;
    color: var(--ink-navy);
    margin-bottom: 10px;
  }
  .contact-list { list-style: none; }
  .contact-item {
    display: flex;
    align-items: center;
    gap: 9px;
    font-size: 14px;
    color: var(--link-blue);
    margin-bottom: 7px;
  }
  .contact-icon {
    width: 15px;
    height: 15px;
    flex: none;
  }
  .eagle-watermark {
    position: absolute;
    left: 90px;
    top: 218px;
    width: 200px;
    height: 70px;
    border-radius: 50%;
    background: radial-gradient(ellipse at 50% 50%, rgba(120,130,145,0.35) 0%, rgba(120,130,145,0.12) 55%, rgba(120,130,145,0) 75%);
  }
</style>
</head>
<body>

  <section class="card card-front" aria-label="Card front">
    <div class="world-globe" role="img" aria-label="World globe showing the Americas">
      <div class="continents"></div>
    </div>
    <p class="tagline">Where there are<br>Open Horizon to<br>Your Success!</p>
  </section>

  <section class="card card-back" aria-label="Card back">
    <div class="brand-band">
      <div class="brand-name"><span class="brand-dot"></span>OPEN HORIZON</div>
    </div>

    <div class="eagle-watermark" role="img" aria-label="Faint eagle in flight watermark"></div>

    <div class="contact-block">
      <p class="contact-name">Dr. Lorna Vickers Dunmore</p>
      <ul class="contact-list">
        <li class="contact-item">
          <svg class="contact-icon" viewBox="0 0 16 16" aria-hidden="true">
            <circle cx="8" cy="8" r="8" fill="var(--ink-navy)"/>
            <path d="M5.2 4.2l1.4-.4 1 2-1 .8a5 5 0 0 0 1.8 1.8l.8-1 2 1-.4 1.4c-3 .3-5.9-2.6-5.6-5.6z" fill="#fff"/>
          </svg>
          (555) 284-9306 US
        </li>
        <li class="contact-item">
          <svg class="contact-icon" viewBox="0 0 16 16" aria-hidden="true">
            <circle cx="8" cy="8" r="8" fill="var(--ink-navy)"/>
            <rect x="4" y="5" width="8" height="6" fill="none" stroke="#fff" stroke-width="1.1"/>
            <path d="M4 5l4 3.2L12 5" fill="none" stroke="#fff" stroke-width="1.1"/>
          </svg>
          lornajeanvickers@mailbox.example
        </li>
        <li class="contact-item">
          <svg class="contact-icon" viewBox="0 0 16 16" aria-hidden="true">
            <circle cx="8" cy="8" r="8" fill="var(--ink-navy)"/>
            <circle cx="8" cy="8" r="4.2" fill="none" stroke="#fff" stroke-width="1"/>
            <ellipse cx="8" cy="8" rx="1.8" ry="4.2" fill="none" stroke="#fff" stroke-width="0.9"/>
            <line x1="3.8" y1="8" x2="12.2" y2="8" stroke="#fff" stroke-width="0.9"/>
          </svg>
          www.ohacad.example
        </li>
      </ul>
    </div>
  </section>

</body>
</html>
```